Garlic Farm for Farm Sales/Restaurant sales

Need a professional, but appealing to agriculture world. We are selling 27 kinds of Organic Garlic from a farm in Simla,CO. I have uploaded logo and business information-we are going to need a template, because I will need to use it for four separate people.
-We are trying to appeal to Farm to table restaurants
-As well as growers/farmers

Target Market(s)

Agriculture Sales/Restaurants-Organic

Industry/Entity Type

Agriculture

Contact Information for Business Card

Want it to look more unique then your average kelto stock card- I want it to look amazing

Font styles to use
Sans Serif

Colors
0455a3
ec1f27
fbed22
ffffff

Requirements
Must have
• Just be creative
Nice to have
• Colorful
Should not have
• plain

```html
<!DOCTYPE html>
<html lang="en">
<head>
<meta charset="UTF-8">
<title>Summit Ridge Garlic – Business Card</title>
<link href="https://fonts.googleapis.com/css2?family=Montserrat:wght@500;600;700&display=swap" rel="stylesheet">
<style>
  :root {
    --navy: #1f2f5e;
    --red: #c8202a;
    --yellow: #fbed22;
    --white: #ffffff;
    --stage: #e9e9ea;
    --photo-light: #f3efe7;
    --photo-mid: #e2d6c2;
    --ghost: #f6ecea;
  }
  * { box-sizing: border-box; margin: 0; padding: 0; }
  html, body { width: 1200px; height: 880px; overflow: hidden; }
  body {
    background: var(--stage);
    font-family: "Montserrat", sans-serif;
    position: relative;
  }
  .card {
    position: absolute;
    left: 270px;
    width: 660px;
    height: 390px;
    background: var(--white);
    box-shadow: 0 6px 18px rgba(0,0,0,.18);
    overflow: hidden;
  }
  .card--front { top: 30px; }
  .card--back { top: 460px; }

  /* front */
  .front-photo {
    position: absolute; inset: 0;
    background: radial-gradient(ellipse at 55% 50%, var(--photo-mid) 0%, var(--photo-light) 70%, var(--white) 100%);
  }
  .front-brand {
    position: absolute; left: 0; right: 0; top: 140px;
    text-align: center; color: var(--navy);
  }
  .front-brand__name { font-size: 54px; font-weight: 700; letter-spacing: 1px; }
  .front-brand__tag { font-size: 20px; font-weight: 600; margin-top: 2px; }
  .front-brand__web { font-size: 18px; font-weight: 600; margin-top: 10px; }

  /* back */
  .back-ghost {
    position: absolute; left: 110px; top: 60px;
    width: 230px; height: 280px;
    background: var(--ghost); border-radius: 50% 50% 45% 45%;
  }
  .social { position: absolute; left: 40px; top: 40px; display: flex; gap: 6px; }
  .social span { width: 24px; height: 24px; background: var(--red); display: block; }

  .logo {
    position: absolute; right: 40px; top: 48px;
    display: flex; align-items: center; gap: 14px;
  }
  .logo__mark { width: 54px; height: 54px; border-radius: 50%; background: var(--red); }
  .logo__name { color: var(--navy); font-size: 34px; font-weight: 700; line-height: 1; }
  .logo__name small { display: block; font-size: 15px; font-weight: 600; margin-top: 4px; }

  .divider {
    position: absolute; left: 40px; right: 40px; top: 180px;
    height: 1px; background: var(--red);
  }
  .address {
    position: absolute; right: 40px; top: 196px;
    text-align: right; color: var(--navy); font-size: 15px; font-weight: 500; line-height: 1.4;
  }
  .person {
    position: absolute; left: 40px; top: 196px; color: var(--navy);
  }
  .person__name { font-size: 24px; font-weight: 700; margin-bottom: 14px; }
  .contact { list-style: none; }
  .contact li {
    display: flex; align-items: center; gap: 10px;
    font-size: 16px; font-weight: 500; margin-bottom: 8px;
  }
  .contact svg { width: 22px; height: 22px; flex: none; }
</style>
</head>
<body>

<section class="card card--front">
  <div class="front-photo" role="img" aria-label="Photo of white garlic bulbs in a woven basket"></div>
  <div class="front-brand">
    <div class="front-brand__name">Summit Ridge</div>
    <div class="front-brand__tag">gourmet garlic</div>
    <div class="front-brand__web">RidgeGarlic.com</div>
  </div>
</section>

<section class="card card--back">
  <div class="back-ghost" role="img" aria-label="Faint illustration of a garlic bulb"></div>

  <div class="social" aria-label="Social media links">
    <span></span><span></span><span></span><span></span>
  </div>

  <div class="logo">
    <div class="logo__mark"></div>
    <div class="logo__name">Summit Ridge<small>gourmet garlic</small></div>
  </div>

  <div class="divider"></div>

  <div class="address">P.O. Box 12 Elmdale,<br>CO 80000</div>

  <div class="person">
    <div class="person__name">Dana Holt</div>
    <ul class="contact">
      <li>
        <svg viewBox="0 0 22 22"><rect width="22" height="22" fill="#c8202a"/><path d="M7 5l3 3-2 2c1 2 2 3 4 4l2-2 3 3-2 2C9 17 5 13 5 7z" fill="#fff"/></svg>
        555-014-2290
      </li>
      <li>
        <svg viewBox="0 0 22 22"><rect width="22" height="22" fill="#c8202a"/><rect x="4" y="6" width="14" height="10" fill="none" stroke="#fff" stroke-width="1.5"/><path d="M4 6l7 6 7-6" fill="none" stroke="#fff" stroke-width="1.5"/></svg>
        dana@ridgegarlic.com
      </li>
      <li>
        <svg viewBox="0 0 22 22"><rect width="22" height="22" fill="#c8202a"/><circle cx="11" cy="11" r="6.5" fill="none" stroke="#fff" stroke-width="1.5"/><ellipse cx="11" cy="11" rx="3" ry="6.5" fill="none" stroke="#fff" stroke-width="1.2"/><path d="M4.5 11h13" stroke="#fff" stroke-width="1.2"/></svg>
        RidgeGarlic.com
      </li>
    </ul>
  </div>
</section>

</body>
</html>
```